New Bicycle shop business card

Hi!
I'm looking for a business card for my new proffesional bike mechanics shop. This shop is only for fixing broken bikes and not selling bikes.
Peferbly a modern and sleek and modern design.
Colors: black, grey, red, white
Information:
Name: Rijwielwerkplaats Vanhoutte
Shop owner: Bart Vanhoutte & Marieke Segers
Website: www.rijwielwerkplaats-vanhoutte.be
Email: info@rijwielwerkplaats-vanhoutte.be
Phone number: +32471902368
Street adres: Kerkweg 46
9940 Bellebeke
Slogan/shop information: Herstellingen van alle merken.
Logo: see files.
Target Market(s)
People who seek a mechanic to fix or upgrade their bikes.
Contact Information for Business Card
Information:
Website: info@rijwielwerkplaats-vanhoutte.be
9940 Bellebeke
Logo: see files.

```html
<!DOCTYPE html>
<html lang="nl">
<head>
<meta charset="utf-8">
<title>Rijwielwerkplaats Vanhoutte – visitekaartje</title>
<link href="https://fonts.googleapis.com/css2?family=Montserrat:wght@700;800&family=Roboto:wght@400&display=swap" rel="stylesheet">
<style>
  :root {
    --backdrop: #e4e4e4;
    --card: #fbfbfb;
    --ink: #1d1d1b;
    --red: #d6263a;
    --grey: #8e9193;
    --text: #2a2a2a;
  }
  * { box-sizing: border-box; margin: 0; padding: 0; }
  html, body { width: 1200px; height: 852px; overflow: hidden; }
  body {
    background: var(--backdrop);
    font-family: "Roboto", Arial, sans-serif;
    color: var(--text);
    position: relative;
  }
  .card {
    position: absolute;
    top: 276px;
    width: 510px;
    height: 300px;
    background: var(--card);
    border-radius: 16px;
    overflow: hidden;
    box-shadow: 0 6px 18px rgba(0,0,0,.12);
  }
  .card--back { left: 70px; }
  .card--front { left: 620px; }

  .brand-name {
    display: block;
    font-family: "Montserrat", Arial, sans-serif;
    font-weight: 800;
    color: var(--ink);
    text-transform: uppercase;
    line-height: 1.1;
  }
  .brand-name .line { display: block; white-space: nowrap; }
  .brand-name .line--wide { letter-spacing: .32em; }

  /* back side */
  .back-brand {
    position: absolute;
    top: 80px; left: 0; right: 0;
    display: flex; align-items: center; justify-content: center; gap: 14px;
  }
  .brand-mark { width: 26px; height: 26px; background: var(--red); border-radius: 4px; flex: none; }
  .back-brand .brand-name { font-size: 22px; text-align: center; }
  .tagline {
    position: absolute;
    top: 190px; left: 0; right: 0;
    display: flex; align-items: center; justify-content: center; gap: 14px;
    font-size: 13px;
  }
  .tagline::before, .tagline::after {
    content: ""; width: 44px; height: 2px; background: var(--red);
  }
  .edge-band { position: absolute; bottom: 0; left: 0; right: 0; height: 12px; display: flex; }
  .edge-band .red { flex: 1; background: var(--red); }
  .edge-band .grey { flex: 1; background: var(--grey); }

  /* front side */
  .front-accent {
    position: absolute;
    top: 20px; right: 24px;
    width: 140px; height: 140px;
    background: var(--red);
    border-radius: 4px;
  }
  .front-brand { position: absolute; top: 84px; left: 28px; }
  .front-brand .brand-name { font-size: 20px; }
  .person { position: absolute; top: 150px; left: 28px; }
  .person-name {
    font-family: "Montserrat", Arial, sans-serif;
    font-weight: 700; font-size: 16px;
    color: var(--red); text-transform: uppercase; letter-spacing: .5px;
  }
  .person-role { font-size: 11px; margin-top: 3px; }
  .contact {
    position: absolute; top: 200px; left: 28px;
    list-style: none; font-size: 11.5px; line-height: 17px;
  }
  .contact li { display: flex; align-items: center; gap: 8px; }
  .contact svg { width: 11px; height: 11px; fill: var(--red); flex: none; }
  .contact .address { padding-left: 19px; }
</style>
</head>
<body>

<section class="card card--back" aria-label="Achterkant">
  <div class="back-brand">
    <span class="brand-mark"></span>
    <span class="brand-name">
      <span class="line">Rijwielwerkplaats</span>
      <span class="line line--wide">Vanhoutte</span>
    </span>
  </div>
  <p class="tagline">Herstellingen van alle merken</p>
  <div class="edge-band"><span class="red"></span><span class="grey"></span></div>
</section>

<section class="card card--front" aria-label="Voorkant">
  <div class="front-accent"></div>
  <div class="front-brand">
    <span class="brand-name">
      <span class="line">Rijwielwerkplaats</span>
      <span class="line line--wide">Vanhoutte</span>
    </span>
  </div>
  <div class="person">
    <p class="person-name">Marieke Segers</p>
    <p class="person-role">Owner</p>
  </div>
  <ul class="contact">
    <li>
      <svg viewBox="0 0 24 24" aria-hidden="true"><path d="M6.6 10.8a15.1 15.1 0 0 0 6.6 6.6l2.2-2.2a1 1 0 0 1 1-.25 11.4 11.4 0 0 0 3.6.57 1 1 0 0 1 1 1V20a1 1 0 0 1-1 1A17 17 0 0 1 3 4a1 1 0 0 1 1-1h3.5a1 1 0 0 1 1 1c0 1.25.2 2.45.57 3.57a1 1 0 0 1-.25 1z"/></svg>
      +32471902368
    </li>
    <li>
      <svg viewBox="0 0 24 24" aria-hidden="true"><path d="M12 2a10 10 0 1 0 0 20 10 10 0 0 0 0-20zm6.9 6h-3a15.7 15.7 0 0 0-1.3-3.9A8 8 0 0 1 18.9 8zM12 4c.8 1.2 1.5 2.5 1.9 4h-3.8c.4-1.5 1.1-2.8 1.9-4zM4.3 14a8.2 8.2 0 0 1 0-4h3.4a16.5 16.5 0 0 0 0 4zm.8 2h3a15.7 15.7 0 0 0 1.3 3.9A8 8 0 0 1 5.1 16zm3-8h-3a8 8 0 0 1 4.3-3.9A15.7 15.7 0 0 0 8.1 8zM12 20c-.8-1.2-1.5-2.5-1.9-4h3.8c-.4 1.5-1.1 2.8-1.9 4zm2.3-6H9.7a14.7 14.7 0 0 1 0-4h4.6a14.7 14.7 0 0 1 0 4zm.3 5.9a15.7 15.7 0 0 0 1.3-3.9h3a8 8 0 0 1-4.3 3.9zm1.7-5.9a16.5 16.5 0 0 0 0-4h3.4a8.2 8.2 0 0 1 0 4z"/></svg>
      www.rijwielwerkplaats-vanhoutte.be
    </li>
    <li>
      <svg viewBox="0 0 24 24" aria-hidden="true"><path d="M2 5h20v14H2z" fill="none"/><path d="M2 5h20v1.5l-10 7-10-7z"/><path d="M2 9l10 7 10-7v10H2z"/></svg>
      info@rijwielwerkplaats-vanhoutte.be
    </li>
    <li class="address">Kerkweg 46 9940 Bellebeke</li>
  </ul>
</section>

</body>
</html>
```